Business card design needed

Family General Practitioner/ Family Physician.
Logo is the logo of the Noble Guild of Family Healers Oceania
http://kpltw.varendo.example/ImageShelf/marks/pages/NGFHO%20mark_jpg.htm
Updates

Project Deadline Extended
Reason: Just a bit more time to make changes and the weekend for me to look at things closely and to choose. Thanks, Orin

Thanks for all the submissions. So many of them are really works of art. Not one of them are not good. The ones that I am eliminating are the ones that I think are not suitable for me personally only, and because if I don't, it makes it very difficult to decide as many of you are also sending me slight variations of a card. I have just decided to choose a second place card too. Can't thank you all enough. Good luck, Orin. P.S - Working today till 10 pm as the card says :-), so probably won't be able to give a feedback till late Saturday night or Sunday morning here in Sydney, Australia. 

Project Deadline Extended
Reason: Just added a second place to the budget and realised that Australia is ahead of the rest of the world in the time zone (only :-) - don't want to offend anyone or start a debate!! ) , so Monday deadline will mean it will be a weekend for the rest of the world. Just wanted to give everyone more time to submit their best, especially since I will be picking a second card too. Can't thank everyone enough for the submissions. P.S - Not keen on photos on the card.

Industry/Entity Type

Business

Contact Information for Business Card

Dr. Orin Halvey M.B.B.S., F.N.G.F.H.O
Family General Practitioner
Address, timings, phone and fax number on the back.

Requirements
Must have
• Timings
Mon 7 am - 7 pm
Tues 7 am - 12 pm
Wed 7 am - 10 pm
Thurs 7 am - 12 pm
Fri 7 am - 8 pm
Sat 8 am - 10 pm
Sun - Off

```html
<!DOCTYPE html>
<html lang="en">
<head>
<meta charset="utf-8">
<title>Dr. Orin Halvey – Business Card Back</title>
<link rel="stylesheet" href="https://fonts.googleapis.com/css2?family=Old+Standard+TT:wght@400;700&display=swap">
<style>
  :root {
    --paper: #ffffff;
    --orange: #ee5a14;
    --peach: #f4c3a6;
    --lavender: #aeb8f0;
    --sky: #bfe4fb;
    --ice: #e6f4fd;
  }
  html, body {
    margin: 0;
    padding: 0;
    overflow: hidden;
    background: var(--paper);
  }
  .card {
    position: relative;
    width: 741px;
    height: 1200px;
    overflow: hidden;
    background: var(--paper);
    font-family: "Old Standard TT", "Century Schoolbook", Georgia, serif;
  }
  .decor {
    position: absolute;
    inset: 0;
  }
  .side-text {
    position: absolute;
    inset: 0;
  }
  .side-text .doctor-name {
    fill: var(--lavender);
    font-size: 150px;
    font-variant: small-caps;
    opacity: 0.85;
  }
  .side-text .specialty,
  .side-text .credentials {
    fill: var(--peach);
    font-size: 31px;
  }
  .details {
    position: absolute;
    left: 273px;
    top: 0;
    color: var(--orange);
    font-size: 31px;
    line-height: 1;
  }
  .details .line {
    position: absolute;
    left: 0;
    white-space: nowrap;
  }
  .hours-title { top: 210px; }
  .hours-row .day { display: inline-block; width: 127px; }
  .appt-label { top: 664px; }
  .appt-rule {
    position: absolute;
    left: 0;
    top: 775px;
    width: 344px;
    height: 2px;
    background: var(--orange);
  }
  .contact .label { display: inline-block; width: 87px; }
</style>
</head>
<body>
  <div class="card">
    <svg class="decor" width="741" height="1200" viewBox="0 0 741 1200" role="img" aria-label="Soft blue starburst flower decoration behind the doctor's name">
      <defs>
        <radialGradient id="bloom" cx="150" cy="650" r="560" gradientUnits="userSpaceOnUse">
          <stop offset="0" stop-color="#ffffff"/>
          <stop offset="0.12" stop-color="var(--sky)"/>
          <stop offset="0.45" stop-color="var(--ice)"/>
          <stop offset="1" stop-color="#ffffff"/>
        </radialGradient>
      </defs>
      <rect width="741" height="1200" fill="url(#bloom)"/>
    </svg>

    <svg class="side-text" width="741" height="1200" viewBox="0 0 741 1200" aria-hidden="false">
      <text class="doctor-name" transform="translate(178,1136) rotate(-90)" textLength="1033" lengthAdjust="spacingAndGlyphs">Dr. Orin Halvey</text>
      <text class="specialty" transform="translate(221,563) rotate(-90)" textLength="444" lengthAdjust="spacingAndGlyphs">Family General Practitioner</text>
      <text class="credentials" transform="translate(225,1136) rotate(-90)" textLength="352" lengthAdjust="spacingAndGlyphs">M.B.B.S., F.N.G.F.H.O</text>
    </svg>

    <div class="details">
      <div class="line hours-title">Office Hours:</div>
      <div class="line hours-row" style="top:295px"><span class="day">Mon.</span>7 am - 7 pm</div>
      <div class="line hours-row" style="top:336px"><span class="day">Tues.</span>7 am - 12 pm</div>
      <div class="line hours-row" style="top:377px"><span class="day">Wed.</span>7 am - 10 pm</div>
      <div class="line hours-row" style="top:418px"><span class="day">Thurs.</span>7 am - 12 pm</div>
      <div class="line hours-row" style="top:459px"><span class="day">Fri.</span>7 am - 8 pm</div>
      <div class="line hours-row" style="top:500px"><span class="day">Sat.</span>8 am - 10 pm</div>
      <div class="line hours-row" style="top:541px"><span class="day">Sun.</span>Closed</div>

      <div class="line appt-label">Appt Time:</div>
      <div class="appt-rule"></div>

      <div class="line contact" style="top:994px"><span class="label">P:</span>02 7431 5096</div>
      <div class="line contact" style="top:1035px"><span class="label">F:</span>02 7431 5087</div>
    </div>
  </div>
</body>
</html>
```